KTR Photography Editing & Support Services for Real Estate

We require a double sided A4 flyer to promote our photography services to real estate agencies.
This particular service is targeted to rural areas where reliable, professional and highly skilled photographers are difficult to source. We teach the agent how to photograph, they upload files to a server and we take care of the rest (image editing, quality control and delivery). This will give the agents flexibility with when to shoot and eliminates the stress of managing a photographer / contractor. We offer a 1 day face to face training session and competitive packages for equipment start up.
We would like the flyer to look clean & very professional. The flyer should showcase samples of our work to highlight what can be achieved by using our services. We like the look of a black or dark background behind the text and feel that would look nice with our photographs provided. Otherwise open to your suggestions and ideas.
TEXT FOR FLYER:
Welcome to the KTR Real Estate Photography Editing and Support Service
• Take your real estate business to the next level by providing impressive real estate imagery that makes you stands out from the competition
• Omit the stress of trying to find a good photographer or managing an unreliable one and hence have more time to focus on other aspects of your business
• Showcase your listings with better quality and more impactful photographs than your competitors thereby increasing potential for a quick sale
• Great first impressions matter and you will achieve this by looking and feeling more professional. This will attract and retain more future clients.
HOW IT WORKS
• We understand that your time is valuable, so let us handle the editing and delivery of your images. You shoot, and we take care of the rest.
• Images are edited and delivered within 1 working day
INCLUSIONS:
• Full day face to face training (we come to you) and instructional handbook
• We will teach you everything you need to know about your equipment and how to take stunning real estate photographs
• Service turnaround within 1 working day
• Free HELP desk service Mon-Fri
• 12 month Exclusivity (rural towns only) for a limited time
INVESTMENT
• 99 per listing for us to manage images including editing, quality control and delivery (10 Images)
• Ask us about competitive packages for photography equipment if required
SUMMARY
The KTR Real Estate Photography Editing and Support Service is the perfect solution for busy real estate professionals who want to take their business to the next level. Our service is affordable, flexible, and designed to help you showcase your listings in the best possible light.
Contact us today to learn more about how we can help you.

```html
<!DOCTYPE html>
<html lang="en">
<head>
<meta charset="utf-8">
<title>KTR Photography Editing &amp; Support Services</title>
<link href="https://fonts.googleapis.com/css2?family=Poppins:wght@300;400;500;600;700&family=Kaushan+Script&display=swap" rel="stylesheet">
<style>
  :root {
    --gold: #b4985a;
    --ink: #1e1e1e;
    --text: #3a3a3a;
    --paper: #ffffff;
    --backdrop: #ffffff;
    --panel: rgba(22, 22, 22, 0.9);
  }
  * { margin: 0; padding: 0; box-sizing: border-box; }
  html, body { width: 815px; height: 1200px; overflow: hidden; background: var(--backdrop); }
  body { font-family: "Poppins", sans-serif; color: var(--text); position: relative; }

  .page { position: absolute; top: 336px; width: 602px; height: 852px; background: var(--paper);
    overflow: hidden; transform: scale(0.62); transform-origin: 0 0;
    box-shadow: 0 0 24px rgba(0,0,0,0.12); }
  .page-front { left: 22px; }
  .page-back { left: 420px; }

  .abs { position: absolute; }

  /* front */
  .corner-block { left: 335px; top: 0; width: 267px; height: 195px; background: var(--ink); }
  .brand { left: 0; top: 30px; width: 335px; text-align: center; }
  .brand-name { display: block; font-weight: 300; font-size: 19px; letter-spacing: 4px; color: #4a4a4a; margin-top: 38px; }
  .brand-role { display: block; font-weight: 400; font-size: 8px; letter-spacing: 2.5px; color: #4a4a4a; margin-top: 4px; }

  .hero { left: 20px; top: 124px; width: 562px; height: 352px; border: 2px solid var(--gold);
    background: linear-gradient(180deg, #8f87b4 0%, #b7a9c6 26%, #a8aeb7 44%, #e2dfd9 68%, #cfc7b8 100%); }
  .welcome { left: 32px; top: 247px; width: 323px; height: 153px; background: var(--panel); padding: 4px 16px; }
  .welcome-script { font-family: "Kaushan Script", cursive; color: var(--gold); font-size: 33px; line-height: 1.2; }
  .welcome-title { font-weight: 700; font-size: 26px; line-height: 0.98; color: #fff; text-transform: uppercase; margin-top: 2px; }
  .welcome-title .accent { color: var(--gold); display: block; }

  .thumb { top: 420px; width: 163px; height: 130px; border: 2px solid #fff; }
  .thumb-lounge { left: 35px; background: linear-gradient(160deg, #5d6772 0%, #2f3339 55%, #1b1c1f 100%); }
  .thumb-bedroom { left: 219px; background: linear-gradient(160deg, #f3f2ef 0%, #dcd9d3 60%, #a9a49b 100%); }
  .thumb-bath { left: 404px; background: linear-gradient(160deg, #e6e1da 0%, #d2c9bd 60%, #b99a72 100%); }

  .section-tab { position: absolute; left: 32px; height: 27px; display: flex; align-items: stretch; }
  .section-tab::before { content: ""; width: 3px; background: var(--gold); margin-right: 4px; }
  .section-tab span { background: var(--ink); color: #fff; font-weight: 700; font-size: 18px;
    padding: 0 32px 0 13px; line-height: 27px; clip-path: polygon(0 0, 88% 0, 100% 100%, 0 100%); }

  .bullets { position: absolute; list-style: none; font-size: 8.4px; line-height: 1.25; color: var(--text); }
  .bullets li { position: relative; padding-left: 13px; margin-bottom: 5px; }
  .bullets li::before { content: ""; position: absolute; left: 1px; top: 2px; width: 6px; height: 6px;
    border-radius: 50%; border: 1.5px solid var(--gold); }

  .footer-gold { left: 300px; top: 788px; width: 302px; height: 64px; background: var(--gold); }
  .footer-dark { left: 0; top: 773px; width: 335px; height: 79px; background: var(--ink);
    clip-path: polygon(0 0, 300px 0, 335px 100%, 0 100%); }
  .phone { left: 32px; top: 792px; display: flex; align-items: center; gap: 10px;
    color: #fff; font-weight: 600; font-size: 28px; line-height: 40px; }
  .email { left: 333px; top: 810px; display: flex; align-items: center; gap: 7px;
    color: #fff; font-weight: 600; font-size: 12px; line-height: 20px; }

  /* back */
  .photo { border: 2px solid var(--gold); }
  .photo-cottage { left: 32px; top: 29px; width: 270px; height: 276px;
    background: linear-gradient(180deg, #6f93c4 0%, #a9bfd8 35%, #4b4a4f 55%, #6c7d4a 85%, #4f7a34 100%); }
  .photo-hallway { left: 310px; top: 29px; width: 259px; height: 134px;
    background: linear-gradient(120deg, #8a6c4c 0%, #d8d4cc 45%, #f2f0ec 100%); }
  .photo-dining { left: 310px; top: 170px; width: 259px; height: 135px;
    background: linear-gradient(180deg, #f4f3f0 0%, #e3ddd3 55%, #a89a86 100%); }
  .photo-lounge { left: 310px; top: 438px; width: 259px; height: 120px;
    background: linear-gradient(180deg, #5a4330 0%, #2f5f9a 35%, #8b6a48 70%, #cfc6b8 100%); }
  .photo-coast { left: 32px; top: 572px; width: 260px; height: 120px;
    background: linear-gradient(180deg, #c9c4d4 0%, #e9c9b3 40%, #557f96 65%, #7b6a52 100%); }
  .portrait { left: 380px; top: 570px; width: 190px; height: 218px;
    background: linear-gradient(180deg, #ffffff 0%, #f1ece6 40%, #2a2a2a 62%, #1d1d1d 100%); }

  .big-price { left: 30px; top: 476px; font-weight: 600; font-size: 40px; line-height: 48px; color: var(--gold); }
  .price-note { left: 92px; top: 486px; width: 175px; font-size: 8.4px; line-height: 1.25; }

  .name-tag { left: 308px; top: 637px; width: 98px; height: 46px; background: var(--gold); padding: 6px 10px; color: #fff; }
  .name-tag strong { display: block; font-weight: 600; font-size: 10.5px; line-height: 1.2; }
  .name-tag span { display: block; font-weight: 400; font-size: 8.5px; line-height: 1.2; }

  .summary { left: 32px; top: 718px; width: 272px; font-size: 6.4px; line-height: 1.3; }
</style>
</head>
<body>

<main class="page page-front">
  <div class="abs corner-block"></div>
  <header class="abs brand">
    <span class="brand-name">DANA MORRELL</span>
    <span class="brand-role">PHOTOGRAPHER</span>
  </header>

  <div class="abs hero" role="img" aria-label="Twilight exterior of a modern white farmhouse with glass gable front"></div>

  <section class="abs welcome">
    <div class="welcome-script">Welcome to the</div>
    <h1 class="welcome-title">KTR Photography<span class="accent">Editing &amp; Support</span>Services</h1>
  </section>

  <div class="abs thumb thumb-lounge" role="img" aria-label="Dark living room with black sofa and cushions"></div>
  <div class="abs thumb thumb-bedroom" role="img" aria-label="Bright bedroom with large windows onto the country"></div>
  <div class="abs thumb thumb-bath" role="img" aria-label="Bathroom with freestanding tub and timber vanity"></div>

  <h2 class="section-tab" style="top:563px"><span>OUR SERVICE</span></h2>
  <ul class="bullets" style="left:34px; top:602px; width:256px;">
    <li>Take your real estate business to the next level by providing impressive real estate imagery that makes you stands out from the competition</li>
    <li>Omit the stress of trying to find a good photographer or managing an unreliable one and hence have more time to focus on other aspects of your business</li>
  </ul>
  <ul class="bullets" style="left:302px; top:602px; width:262px;">
    <li>Showcase your listings with better quality and more impactful photographs than your competitors thereby increasing potential for a quick sale</li>
    <li>Great first impressions matter and you will achieve this by looking and feeling more professional. This will attract and retain more future clients.</li>
  </ul>

  <h2 class="section-tab" style="top:683px"><span>HOW IT WORKS</span></h2>
  <ul class="bullets" style="left:34px; top:722px; width:530px;">
    <li>We understand that your time is valuable, so let us handle the editing and delivery of your images. You shoot, and we take care of the rest.</li>
    <li>Images are edited and delivered within 1 working day</li>
  </ul>

  <footer>
    <div class="abs footer-gold"></div>
    <div class="abs footer-dark"></div>
    <div class="abs phone">
      <svg width="22" height="22" viewBox="0 0 24 24" aria-hidden="true"><path fill="#fff" d="M6.6 10.8a15.1 15.1 0 0 0 6.6 6.6l2.2-2.2c.3-.3.7-.4 1-.2 1.1.4 2.3.6 3.6.6.6 0 1 .4 1 1V20c0 .6-.4 1-1 1A17 17 0 0 1 3 4c0-.6.4-1 1-1h3.5c.6 0 1 .4 1 1 0 1.3.2 2.5.6 3.6.1.3 0 .7-.2 1z"/></svg>
      <span>61 400 555 019</span>
    </div>
    <div class="abs email">
      <svg width="13" height="10" viewBox="0 0 18 14" aria-hidden="true"><rect width="18" height="14" rx="1.5" fill="#fff"/><path d="M1 1.5 9 8l8-6.5" fill="none" stroke="#b4985a" stroke-width="1.6"/></svg>
      <span>shoot@danamorrell.com.au</span>
    </div>
  </footer>
</main>

<main class="page page-back">
  <div class="abs photo photo-cottage" role="img" aria-label="Dark weatherboard cottage at dusk with gravel garden path"></div>
  <div class="abs photo photo-hallway" role="img" aria-label="Hallway with timber bench, pot plant and artwork"></div>
  <div class="abs photo photo-dining" role="img" aria-label="White kitchen and dining room with timber beams"></div>

  <h2 class="section-tab" style="top:320px"><span>INCLUSIONS</span></h2>
  <ul class="bullets" style="left:34px; top:366px; width:250px;">
    <li>Full day face to face training (we come to you) and instructional handbook</li>
    <li>We will teach you everything you need to know about your equipment and how to take stunning real estate photographs</li>
  </ul>
  <ul class="bullets" style="left:305px; top:366px; width:275px;">
    <li>Service turnaround within 1 working day</li>
    <li>Free HELP desk service Mon-Fri</li>
    <li>12 month Exclusivity (rural towns only) for a limited time</li>
  </ul>

  <h2 class="section-tab" style="top:442px"><span>INVESTMENT</span></h2>
  <div class="abs big-price">99</div>
  <p class="abs price-note">per listing for us to manage images including editing, quality control and delivery (10 Images)</p>
  <ul class="bullets" style="left:34px; top:536px; width:220px;">
    <li>Ask us about competitive packages for photography equipment if required</li>
  </ul>

  <div class="abs photo photo-lounge" role="img" aria-label="Open lounge with tall windows onto mountain views"></div>
  <div class="abs photo photo-coast" role="img" aria-label="Dark clad house overlooking a coastal headland at dusk"></div>
  <div class="abs portrait" role="img" aria-label="Portrait of the photographer in a black t-shirt, arms folded"></div>

  <div class="abs name-tag"><strong>DANA MORRELL</strong><span>Photographer</span></div>

  <p class="abs summary">The KTR Real Estate Photography Editing and Support Service is the perfect solution for busy real estate professionals who want to take their business to the next level. Our service is affordable, flexible, and designed to help you showcase your listings in the best possible light.</p>

  <footer>
    <div class="abs footer-gold"></div>
    <div class="abs footer-dark"></div>
    <div class="abs phone">
      <svg width="22" height="22" viewBox="0 0 24 24" aria-hidden="true"><path fill="#fff" d="M6.6 10.8a15.1 15.1 0 0 0 6.6 6.6l2.2-2.2c.3-.3.7-.4 1-.2 1.1.4 2.3.6 3.6.6.6 0 1 .4 1 1V20c0 .6-.4 1-1 1A17 17 0 0 1 3 4c0-.6.4-1 1-1h3.5c.6 0 1 .4 1 1 0 1.3.2 2.5.6 3.6.1.3 0 .7-.2 1z"/></svg>
      <span>61 400 555 019</span>
    </div>
    <div class="abs email">
      <svg width="13" height="10" viewBox="0 0 18 14" aria-hidden="true"><rect width="18" height="14" rx="1.5" fill="#fff"/><path d="M1 1.5 9 8l8-6.5" fill="none" stroke="#b4985a" stroke-width="1.6"/></svg>
      <span>shoot@danamorrell.com.au</span>
    </div>
  </footer>
</main>

</body>
</html>
```